Brellwick Partners, LLC Stationary

Brellwick Partners, LLC is a new financial planning and consulting company. We are looking for designs on business cards, letterhead, envelopes, and anything else that would be useful. Our preference for business card design is two sided. We are looking for a professional and clean look with incorporating the logo and patriotic feel. Thank you to all who participate and good luck!

```html
<!DOCTYPE html>
<html lang="en">
<head>
<meta charset="utf-8">
<title>Brellwick Partners, LLC — Stationery</title>
<link rel="stylesheet" href="https://fonts.googleapis.com/css2?family=Questrial&display=swap">
<style>
  :root {
    --navy: #1f4468;
    --navy-deep: #0d365c;
    --red: #b42a30;
    --paper: #f1f1f1;
    --backdrop: #e6e6e6;
    --ink: #555a60;
  }
  * { margin: 0; padding: 0; box-sizing: border-box; }
  html, body { width: 1200px; height: 821px; overflow: hidden; }
  body {
    position: relative;
    background: var(--backdrop);
    font-family: "Questrial", Arial, sans-serif;
    color: var(--ink);
  }
  .sheet {
    position: absolute;
    background: var(--paper);
    box-shadow: 0 2px 6px rgba(0,0,0,0.12);
  }
  .brand {
    position: absolute;
    display: flex;
    align-items: center;
    gap: 7px;
  }
  .brand-dot {
    width: 12px; height: 12px;
    border-radius: 50%;
    background: var(--navy);
    flex: none;
  }
  .brand-name {
    font-size: 15px;
    letter-spacing: 0.5px;
    color: var(--navy);
    white-space: nowrap;
  }
  .brand-tagline {
    position: absolute;
    font-size: 5px;
    letter-spacing: 0.6px;
    color: var(--red);
    text-transform: uppercase;
    white-space: nowrap;
  }

  /* Letterhead */
  .letterhead { left: 70px; top: 110px; width: 466px; height: 661px; }
  .letterhead .brand { left: 24px; top: 43px; }
  .letterhead .brand-tagline { left: 43px; top: 62px; }
  .letterhead-rule {
    position: absolute;
    left: 32px; top: 598px;
    width: 404px; height: 2px;
    background: linear-gradient(to right, var(--navy) 0 75%, var(--red) 75% 100%);
  }
  .contact-list {
    position: absolute;
    left: 32px; top: 610px;
    list-style: none;
    font-size: 8px;
    line-height: 12px;
  }
  .contact-list li { display: flex; align-items: center; gap: 4px; }
  .contact-list svg { width: 7px; height: 7px; fill: var(--navy); }
  .address-block {
    position: absolute;
    right: 30px; top: 610px;
    text-align: right;
    font-size: 8px;
    line-height: 12px;
  }
  .web { color: var(--navy); letter-spacing: 1px; }

  /* Envelope front */
  .envelope-front { left: 612px; top: 224px; width: 524px; height: 250px; }
  .envelope-front .brand { left: 24px; top: 29px; }
  .envelope-front .brand-tagline { left: 43px; top: 48px; }
  .return-address {
    position: absolute;
    left: 23px; top: 216px;
    font-size: 8px;
    line-height: 10px;
  }

  /* Envelope back */
  .envelope-back { left: 619px; top: 514px; width: 523px; height: 248px; }
  .envelope-flap {
    position: absolute;
    left: 0; top: 0;
    width: 100%; height: 89px;
    background: var(--navy-deep);
    border-radius: 0 0 10px 10px;
  }
</style>
</head>
<body>

  <section class="sheet letterhead" aria-label="Letterhead">
    <div class="brand">
      <span class="brand-dot"></span>
      <span class="brand-name">BRELLWICK PARTNERS, LLC</span>
    </div>
    <div class="brand-tagline">Financial planning and consulting</div>

    <div class="letterhead-rule"></div>
    <ul class="contact-list">
      <li><svg viewBox="0 0 10 10"><path d="M2 0.5 L3.8 0.5 L4.5 3 L3.3 4 Q4.3 6 6 6.8 L7 5.6 L9.5 6.3 L9.5 8.2 Q9.5 9.5 8 9.5 Q0.5 8.5 0.5 2 Q0.5 0.5 2 0.5 Z"/></svg>555 210 4478</li>
      <li><svg viewBox="0 0 10 10"><rect x="2.5" y="0.5" width="5" height="3"/><rect x="0.5" y="4" width="9" height="4"/><rect x="2.5" y="7" width="5" height="2.5"/></svg>555 210 4479</li>
      <li><svg viewBox="0 0 10 10"><path d="M0.5 2 H9.5 V8 H0.5 Z M1 2.5 L5 5.5 L9 2.5" fill="none" stroke="#1f4468" stroke-width="1"/></svg>hello@brellwick.com</li>
    </ul>
    <div class="address-block">
      <div>4120 Linden Court</div>
      <div>Juneau, Alaska 99801</div>
      <div class="web">www.brellwick.com</div>
    </div>
  </section>

  <section class="sheet envelope-front" aria-label="Envelope front">
    <div class="brand">
      <span class="brand-dot"></span>
      <span class="brand-name">BRELLWICK PARTNERS, LLC</span>
    </div>
    <div class="brand-tagline">Financial planning and consulting</div>
    <div class="return-address">
      <div>4120 Linden Court</div>
      <div>Juneau, Alaska 99801</div>
    </div>
  </section>

  <section class="sheet envelope-back" aria-label="Envelope back">
    <div class="envelope-flap"></div>
  </section>

</body>
</html>
```